Varnik Holdings — Business Card Design Brief
Overview
Design a double-sided business card for Varnik Holdings that highlights our two service arms: Varnik Communications (telecommunications) and Varnik Energy (business energy solutions). The card should feel smart and stand out when handed to clients.

Objectives
Showcase our areas of specialty clearly.
Reflect the overall Varnik / Varnik Holdings brand while acknowledging both arms.
Explore using both logos (Communications + Energy) or one unified logo, depending on the design.

Deliverables
One double-sided business card design (front + back).

Content & Copy
Front (preferred): Logo: Varnik / Varnik Holdings
Descriptor: Business Communications | Business Energy
Back:My contact details and company details
Core products: Business Mobile • Telephony • Internet • Business Energy Solutions

Brand & Visual Direction
We have a group logo currently tailored more toward telecoms, plus a separate Varnik Energy logo.
Please explore layouts that use both logos or just one, whichever works best.
Color: I wouldn't mind seeing an option using our the Blue/Purple gradient from our website (varnik-example.co.uk), but also open to non-gradient approaches and other colours..

Overall look: Smart, modern, and distinctive.
Format & Print Specs
Double-sided business card format. (Use a standard size

Must-Haves
Front: Varnik wording or Varnik Holdings wording with atleast 1 logo also on front “Business Communications | Business Energy.”

Back: Contact + company details and core products.
A design that stands out while remaining professional.

Nice-to-Have Options
A gradient version using our site’s Blue/Purple gradient.
A non-gradient version.
A dual-logo treatment versus a single-logo treatment.

Thanks
Owen

```html
<!DOCTYPE html>
<html lang="en">
<head>
<meta charset="utf-8">
<title>Varnik Holdings Business Card</title>
<link rel="stylesheet" href="https://fonts.googleapis.com/css2?family=Poppins:wght@600;700&family=Lato:wght@400&display=swap">
<style>
  :root {
    --navy: #1c1464;
    --blue: #1565d8;
    --cyan: #10b2e0;
    --white: #ffffff;
    --backdrop: #e9e7e3;
  }
  * { margin: 0; padding: 0; box-sizing: border-box; }
  html, body { width: 1189px; height: 1200px; overflow: hidden; background: var(--backdrop); }
  .canvas { position: relative; width: 1189px; height: 1200px; }
  .card {
    position: absolute; left: 169px; width: 851px; height: 484px;
    border-radius: 33px; overflow: hidden;
    box-shadow: 0 6px 18px rgba(0,0,0,.18);
  }
  .card-front { top: 112px; background: var(--white); }
  .card-back { top: 641px; background: linear-gradient(90deg, #0d5fd9 0%, #0ab4e2 100%); }
  .wave { position: absolute; inset: 0; width: 851px; height: 484px; }

  .brand-mark { position: absolute; left: 64px; top: 64px; width: 104px; height: 104px; border-radius: 50%; background: var(--blue); }
  .brand-name {
    position: absolute; left: 62px; top: 176px;
    font-family: 'Poppins', sans-serif; font-weight: 700; font-size: 64px; line-height: 1;
    color: var(--navy); letter-spacing: 0.5px;
  }
  .brand-descriptor {
    position: absolute; left: 64px; top: 248px;
    font-family: 'Lato', sans-serif; font-size: 16px; line-height: 1; color: var(--navy);
  }
  .person { position: absolute; right: 44px; top: 74px; text-align: right; color: var(--navy); }
  .person-name { font-family: 'Poppins', sans-serif; font-weight: 600; font-size: 28px; line-height: 1.1; }
  .person-role { font-family: 'Lato', sans-serif; font-size: 24px; line-height: 1.3; }

  .company-name {
    position: absolute; right: 44px; top: 322px;
    font-family: 'Poppins', sans-serif; font-weight: 600; font-size: 30px; line-height: 1; color: var(--white);
  }
  .contact-list { position: absolute; right: 37px; top: 372px; list-style: none; }
  .contact-item {
    display: flex; justify-content: flex-end; align-items: center; gap: 9px;
    height: 28px; font-family: 'Lato', sans-serif; font-size: 20px; color: var(--white);
  }
  .contact-icon { width: 22px; height: 22px; }

  .social-list { position: absolute; left: 47px; top: 421px; display: flex; gap: 13px; list-style: none; }
  .social-dot { width: 32px; height: 32px; border-radius: 50%; background: var(--white); }

  .back-mark { position: absolute; left: 370px; top: 130px; width: 112px; height: 112px; border-radius: 50%; background: var(--white); }
  .back-name {
    position: absolute; left: 0; right: 0; top: 288px; text-align: center;
    font-family: 'Poppins', sans-serif; font-weight: 600; font-size: 58px; line-height: 1; color: var(--white);
  }
  .back-products {
    position: absolute; left: 0; right: 0; top: 372px; text-align: center;
    font-family: 'Lato', sans-serif; font-size: 20px; line-height: 1; color: var(--white);
  }
</style>
</head>
<body>
<main class="canvas">
  <section class="card card-front" aria-label="Card front">
    <svg class="wave" viewBox="0 0 851 484" aria-hidden="true">
      <defs>
        <linearGradient id="waveBlue" x1="0" y1="0" x2="1" y2="0">
          <stop offset="0" stop-color="#1565d8"/>
          <stop offset="1" stop-color="#10b2e0"/>
        </linearGradient>
      </defs>
      <path d="M0,262 C90,357 230,372 380,320 C530,268 700,210 851,230 L851,484 L0,484 Z" fill="url(#waveBlue)"/>
      <path d="M0,290 C90,385 230,400 380,348 C530,296 700,238 851,258 L851,484 L0,484 Z" fill="#ffffff"/>
      <path d="M0,300 C90,395 230,410 380,358 C530,306 700,248 851,268 L851,484 L0,484 Z" fill="#1c1464"/>
    </svg>

    <span class="brand-mark" aria-hidden="true"></span>
    <div class="brand-name">VARNIK</div>
    <div class="brand-descriptor">Business Communications | Business Energy</div>

    <div class="person">
      <div class="person-name">DANIEL REEVE</div>
      <div class="person-role">Business development manager</div>
    </div>

    <div class="company-name">VARNIK HOLDINGS</div>
    <ul class="contact-list">
      <li class="contact-item">206-555-0142
        <svg class="contact-icon" viewBox="0 0 22 22" aria-hidden="true"><circle cx="11" cy="11" r="11" fill="#1e88e5"/><path d="M6,9 C6,6 16,6 16,9 L14,10 L13,8.5 L9,8.5 L8,10 Z M8,11 L14,11 L15,15 L7,15 Z" fill="#fff"/></svg>
      </li>
      <li class="contact-item">daniel@varnik-mail.com
        <svg class="contact-icon" viewBox="0 0 22 22" aria-hidden="true"><circle cx="11" cy="11" r="11" fill="#1e88e5"/><rect x="5.5" y="7" width="11" height="8" fill="#fff"/><path d="M5.5,7 L11,11.5 L16.5,7" fill="none" stroke="#1e88e5" stroke-width="1.2"/></svg>
      </li>
      <li class="contact-item">www.varnik-example.co.uk
        <svg class="contact-icon" viewBox="0 0 22 22" aria-hidden="true"><circle cx="11" cy="11" r="11" fill="#1e88e5"/><g fill="none" stroke="#fff" stroke-width="1.1"><circle cx="11" cy="11" r="6"/><ellipse cx="11" cy="11" rx="2.6" ry="6"/><path d="M5,11 H17 M6,8 H16 M6,14 H16"/></g></svg>
      </li>
    </ul>

    <ul class="social-list" aria-label="Social profiles">
      <li class="social-dot"></li>
      <li class="social-dot"></li>
      <li class="social-dot"></li>
    </ul>
  </section>

  <section class="card card-back" aria-label="Card back">
    <span class="back-mark" aria-hidden="true"></span>
    <div class="back-name">VARNIK HOLDINGS</div>
    <div class="back-products">Business Mobile • Telephony • Internet • Business Energy Solutions</div>
  </section>
</main>
</body>
</html>
```